Oil Field Service company needs professional business cards

Looking to clean up our current company business cards and look a little more professional. Brenwick Casing Services is a US based company that services the oil field. We deal with engineers, managers and oil rigs....................................................................................................................................................................................................................................................................................................................................................................................................

Target Market(s)

Oil and Gas professionals

Industry/Entity Type

Oil And Gas

Contact Information for Business Card

See attached photo as example

Font styles to use
Sans Serif

Colors
ec1f27

Requirements
Must have
• Company Logo, Name, Title, Cell, Office, Fax, Email.
• See attached photo
Nice to have
• External CRT, Internal CRT, Casing Crews, Torque Turn, Laydown Machine
Should not have
• Do not introduce any new pictures and keep it professional looking

```html
<!DOCTYPE html>
<html lang="en">
<head>
<meta charset="utf-8">
<title>Brenwick Casing Services – Business Cards</title>
<link href="https://fonts.googleapis.com/css2?family=Open+Sans:wght@400;600;700;800&display=swap" rel="stylesheet">
<style>
  :root {
    --brand-red: #ec1f27;
    --slate: #44525e;
    --slate-light: #6a7782;
    --ink: #555c63;
    --paper: #ffffff;
    --backdrop: #e6e7e9;
  }
  * { box-sizing: border-box; margin: 0; padding: 0; }
  html, body { width: 1200px; height: 950px; overflow: hidden; }
  body {
    background: var(--backdrop);
    font-family: "Open Sans", Arial, sans-serif;
    position: relative;
  }

  /* ---------- front card ---------- */
  .card-front {
    position: absolute;
    left: 110px; top: 160px;
    width: 360px; height: 630px;
    background: var(--paper);
    overflow: hidden;
    box-shadow: 0 10px 30px rgba(0,0,0,.18);
  }
  .card-front .bands { position: absolute; inset: 0; }
  .front-content {
    position: relative;
    display: flex; flex-direction: column; align-items: center;
    padding-top: 70px;
    text-align: center;
    color: var(--ink);
  }
  .wordmark {
    font-weight: 800;
    color: var(--slate);
    line-height: 1;
  }
  .front-content .wordmark-name { font-size: 38px; letter-spacing: 1px; }
  .front-content .wordmark-sub { font-size: 12px; letter-spacing: 4px; margin-top: 5px; }
  .person-icon { margin-top: 22px; }
  .holder-name {
    font-size: 22px; font-weight: 800; color: var(--brand-red);
    margin-top: 4px; letter-spacing: .5px;
  }
  .holder-title {
    font-size: 16px; font-weight: 800; color: var(--slate);
    letter-spacing: 1px; margin-top: 2px;
  }
  .contact-list { list-style: none; margin-top: 16px; }
  .contact-list li {
    display: flex; flex-direction: column; align-items: center;
    font-size: 15px; margin-bottom: 12px; letter-spacing: .5px;
  }
  .contact-list li svg { margin-bottom: 4px; }
  .contact-list .cell { font-weight: 700; color: #3d4349; }

  /* ---------- back card ---------- */
  .card-back {
    position: absolute;
    left: 520px; top: 295px;
    width: 600px; height: 360px;
    background: var(--slate);
    color: var(--paper);
    box-shadow: 0 10px 30px rgba(0,0,0,.18);
    display: flex; flex-direction: column; align-items: center; justify-content: center;
  }
  .card-back .wordmark { color: var(--paper); }
  .card-back .wordmark-name { font-size: 76px; letter-spacing: 2px; }
  .card-back .wordmark-sub { font-size: 20px; letter-spacing: 7px; margin-top: 10px; }
  .rule { width: 60px; height: 4px; background: var(--brand-red); margin: 22px 0 18px; }
  .service-list {
    font-size: 15px; font-style: italic; font-weight: 400;
    text-align: center; line-height: 1.6; letter-spacing: .5px;
  }
</style>
</head>
<body>

<section class="card-front" aria-label="Business card front">
  <svg class="bands" width="360" height="630" viewBox="0 0 360 630" aria-hidden="true">
    <defs>
      <linearGradient id="slateFade" x1="0" y1="0" x2="1" y2="1">
        <stop offset="0" stop-color="#44525e"/>
        <stop offset="1" stop-color="#6a7782"/>
      </linearGradient>
    </defs>
    <path d="M0 0 H360 V60 Q180 -5 0 62 Z" fill="#ec1f27"/>
    <path d="M0 450 Q110 560 360 590 V630 H0 Z" fill="url(#slateFade)"/>
    <path d="M0 450 Q110 560 360 590" fill="none" stroke="#ffffff" stroke-width="3"/>
  </svg>

  <div class="front-content">
    <div class="wordmark">
      <div class="wordmark-name">BRENWICK</div>
      <div class="wordmark-sub">CASING SERVICES</div>
    </div>

    <svg class="person-icon" width="20" height="20" viewBox="0 0 20 20" aria-hidden="true">
      <circle cx="10" cy="6" r="4.5" fill="#ec1f27"/>
      <path d="M1 20 Q1 11 10 11 Q19 11 19 20 Z" fill="#ec1f27"/>
    </svg>
    <div class="holder-name">CODY HARLAN</div>
    <div class="holder-title">AREA MANAGER</div>

    <ul class="contact-list">
      <li>
        <svg width="12" height="16" viewBox="0 0 12 16" aria-hidden="true"><path d="M6 0 A6 6 0 0 1 12 6 C12 10 6 16 6 16 C6 16 0 10 0 6 A6 6 0 0 1 6 0 Z" fill="#ec1f27"/><circle cx="6" cy="6" r="2.2" fill="#fff"/></svg>
        Alden, OK 73822
      </li>
      <li>
        <svg width="14" height="14" viewBox="0 0 14 14" aria-hidden="true"><path d="M3 0 L5.5 3.5 L4 5.5 Q6 9 8.5 10 L10.5 8.5 L14 11 L12 14 Q4 13 0 2 Z" fill="#ec1f27"/></svg>
        (555)410-2700
      </li>
      <li class="cell">
        <svg width="11" height="16" viewBox="0 0 11 16" aria-hidden="true"><rect x="0.8" y="0.8" width="9.4" height="14.4" rx="1.5" fill="none" stroke="#ec1f27" stroke-width="1.6"/><circle cx="5.5" cy="12.5" r="1" fill="#ec1f27"/></svg>
        (555)418-6392
      </li>
      <li>
        <svg width="16" height="14" viewBox="0 0 16 14" aria-hidden="true"><rect x="4" y="0" width="8" height="4" fill="#ec1f27"/><rect x="0" y="5" width="16" height="6" rx="1" fill="#ec1f27"/><rect x="4" y="9" width="8" height="5" fill="#ec1f27"/></svg>
        (555)410-2730
      </li>
      <li>
        <svg width="16" height="11" viewBox="0 0 16 11" aria-hidden="true"><rect width="16" height="11" rx="1" fill="#ec1f27"/><path d="M0.5 0.5 L8 6 L15.5 0.5" fill="none" stroke="#fff" stroke-width="1.3"/></svg>
        cody@brenwick.com
      </li>
      <li>
        <svg width="15" height="15" viewBox="0 0 15 15" aria-hidden="true"><circle cx="7.5" cy="7.5" r="7" fill="#ec1f27"/><ellipse cx="7.5" cy="7.5" rx="3" ry="7" fill="none" stroke="#fff" stroke-width="1"/><line x1="0.5" y1="7.5" x2="14.5" y2="7.5" stroke="#fff" stroke-width="1"/></svg>
        www.brenwick.com
      </li>
    </ul>
  </div>
</section>

<section class="card-back" aria-label="Business card back">
  <div class="wordmark">
    <div class="wordmark-name">BRENWICK</div>
    <div class="wordmark-sub">CASING SERVICES</div>
  </div>
  <div class="rule"></div>
  <p class="service-list">
    External CRT | Internal CRT | Casing Crews<br>
    Torque Turn | Laydown Machine
  </p>
</section>

</body>
</html>
```